Post Disaster Temporary Housing Literature Review poster

Wanting a poster design for two Emergency Management conferences we have coming up. The information to be included in the poster is capturing the purpose, findings and recommendations from a post disaster temporary housing literature review looking at “What should government consider in order to improve planning and decision making for accommodation needs after a disaster, and to support people’s transition to stable housing?”
I’d like to enhance the visual appeal through including relevant images or graphic. I am also open to reducing the text if needed.
The government group I work with focuses on the social and human side of disaster recovery so keen for any images to reflect the human aspect and not focus solely on disasters or housing.
Government and NGO's

```html
<!DOCTYPE html>
<html lang="en">
<head>
<meta charset="utf-8">
<title>Post Disaster Temporary Housing Literature Review</title>
<link href="https://fonts.googleapis.com/css2?family=Poppins:wght@400;500;600;700;800&display=swap" rel="stylesheet">
<style>
:root{
  --plum:#7b2572;
  --plum-dark:#5e1a57;
  --gold:#f5c536;
  --ink:#222;
  --teal:#1f97c9;
  --sky:#a9e3f7;
  --pink-tint:#fdeefc;
  --charcoal:#2b2b2b;
  --magenta:#d055c9;
  --white:#fff;
}
*{box-sizing:border-box;margin:0;padding:0}
html,body{width:802px;height:1200px;overflow:hidden;background:var(--white)}
body{font-family:"Poppins",sans-serif;color:var(--ink);position:relative}
.poster{width:802px;height:1200px;position:relative}

.header{position:absolute;left:0;top:0;width:802px;height:160px;background:var(--plum)}
.header h1{position:absolute;left:56px;top:30px;font-size:35px;line-height:34px;font-weight:800;color:var(--white);letter-spacing:.3px}
.header h1 .accent{color:var(--gold)}
.hero-art{position:absolute;right:20px;top:8px;width:260px;height:150px;border-radius:60px 80px 40px 90px;background:linear-gradient(135deg,#b58be0 0%,#47c3e8 55%,#1fb3a8 100%)}

.section-title{display:flex;align-items:center;gap:8px;font-weight:700;font-size:20px;color:var(--ink)}
.badge{width:30px;height:30px;border-radius:50%;background:var(--plum);display:flex;align-items:center;justify-content:center}

.purpose{position:absolute;left:56px;top:180px;width:280px}
.purpose p{margin-top:10px;font-size:7.4px;line-height:9.2px}
.question{position:absolute;left:418px;top:190px;width:290px;font-size:7.4px;line-height:9.2px}
.question .lead{color:var(--plum);font-weight:700}
.question .ask{color:var(--plum);font-weight:700;margin-top:7px}
.question .note{margin-top:8px}

.findings{position:absolute;left:56px;top:300px}
.finding-row{position:absolute;left:56px;top:340px;width:690px;display:flex;gap:12px}
.finding{flex:1;height:228px;border:1.4px solid var(--plum);border-radius:9px;position:relative;padding:52px 10px 0 9px;font-size:7.1px;line-height:8.9px}
.finding.tinted{background:var(--pink-tint)}
.finding .num{position:absolute;left:-1px;top:-1px;width:44px;height:34px;background:var(--plum);color:var(--white);font-size:17px;font-weight:500;border-radius:9px 0 22px 0;display:flex;align-items:center;justify-content:center}
.finding h3{position:absolute;left:50px;top:6px;right:4px;font-size:9.4px;line-height:11.5px;font-weight:700;color:var(--plum)}
.finding ul{list-style:none;margin-top:8px}
.finding li{position:relative;padding-left:10px;margin-bottom:9px}
.finding li::before{content:"";position:absolute;left:0;top:2px;width:5px;height:5px;border-radius:50%;background:var(--teal)}

.recs-title{position:absolute;left:56px;top:580px;font-size:19px;font-weight:700}
.recs-left{position:absolute;left:56px;top:612px;width:268px}
.recs-right{position:absolute;left:417px;top:766px;width:272px}
.rec{margin-bottom:8px}
.rec h4{display:flex;align-items:center;gap:7px;font-size:10px;font-weight:700;color:var(--teal);line-height:14px}
.rec .hex{width:14px;height:14px;flex:none}
.rec p{font-size:6.3px;line-height:7.7px;margin-top:1px;color:#333}

.research{position:absolute;left:413px;top:612px;width:275px;height:145px;background:var(--plum);color:var(--white);padding:10px 10px 0 6px}
.research h4{display:flex;align-items:center;gap:6px;font-size:11px;font-weight:700}
.research .intro{color:var(--gold);font-weight:700;font-size:6.4px;margin-top:6px}
.research ul{list-style:none;margin-top:5px}
.research li{position:relative;padding-left:15px;font-size:6.2px;line-height:7.6px;font-weight:700;margin-bottom:7px}
.research li::before{content:"";position:absolute;left:4px;top:1px;width:5px;height:5px;border-radius:50%;background:var(--teal)}

.next{position:absolute;left:0;top:937px;width:802px;height:70px;background:var(--sky)}
.next-tab{position:absolute;left:325px;top:-8px;width:152px;height:34px;background:var(--plum);color:var(--white);border-radius:0 0 22px 22px;font-size:18px;font-weight:800;display:flex;align-items:center;justify-content:center}
.next p{position:absolute;left:60px;right:60px;top:33px;font-size:7.2px;line-height:8.8px;text-align:center}

.contact{position:absolute;left:0;top:1007px;width:802px;height:193px;background:var(--charcoal);color:var(--white)}
.contact h2{text-align:center;font-size:18px;font-weight:700;margin-top:10px;letter-spacing:.3px}
.org{position:absolute;left:110px;top:70px;display:flex;align-items:center;gap:12px}
.org .dot{width:58px;height:58px;border-radius:50%;border:2px solid #3aa0d6}
.org .name{font-size:13px;line-height:16px;font-weight:400}
.person{position:absolute;left:395px;top:50px}
.person .who{font-size:18px;font-weight:700;color:var(--magenta)}
.person .role{font-size:9.5px;line-height:12px;font-weight:700;font-style:italic;color:var(--teal);margin-top:3px}
.person .mail{display:flex;align-items:center;gap:6px;font-size:9.5px;margin-top:10px}
</style>
</head>
<body>
<main class="poster">

  <header class="header">
    <h1>POST DISASTER<br>TEMPORARY HOUSING<br><span class="accent">LITERATURE REVIEW</span></h1>
    <div class="hero-art" role="img" aria-label="Illustration of people inspecting and planning around a house, with trees and a location pin"></div>
  </header>

  <section class="purpose">
    <div class="section-title">
      <span class="badge"><svg width="18" height="18" viewBox="0 0 18 18" fill="none" stroke="#fff" stroke-width="1.3"><circle cx="9" cy="9" r="7"/><circle cx="9" cy="9" r="4"/><circle cx="9" cy="9" r="1.2"/><path d="M9 9l6-6"/></svg></span>
      PURPOSE
    </div>
    <p>There are currently significant challenges in supporting displaced people with timely and equitable access to emergency and temporary accommodation and assisting them on a path to stable housing in the aftermath of a disaster. This report seeks to support agencies and decision makers to formulate and implement appropriate approaches to post-disaster housing, factoring in the scale of a disaster and varying community cohorts.</p>
  </section>

  <section class="question">
    <p class="lead">The central research question underpinning this report is:</p>
    <p class="ask">What should government consider in order to improve planning and decision making for accommodation needs after a disaster, and to support people’s transition to stable housing?</p>
    <p class="note">The full report was commissioned by the Community Recovery Advisory Group (CRAG) and undertaken by Mara Ellison and Peter Cole through the Eastbank Institute of Technology (EIT). The findings and recommendations may be utilised by stakeholders.</p>
  </section>

  <div class="section-title findings">
    <span class="badge"><svg width="18" height="18" viewBox="0 0 18 18" fill="none" stroke="#fff" stroke-width="1.3"><circle cx="7" cy="7" r="4.5"/><path d="M10.5 10.5l5 5"/></svg></span>
    FINDINGS
  </div>

  <section class="finding-row">
    <article class="finding">
      <span class="num">01</span>
      <h3>LEADING PRACTICE IN DISASTER HOUSING RECOVERY</h3>
      <p>The analysis of leading practices in housing recovery led to the development of a checklist of actions that could be used to identify appropriate actions by housing recovery officers and their agencies in providing and managing emergency and short-term accommodation and temporary housing. The checklist was developed from research and contains criteria for achieving eight categories of leading practice: Community Engagement &amp; Participation, Location, Safety, Health, Comfort &amp; Privacy, Cultural &amp; Special Needs, Community &amp; Connection, and Social &amp; Technical Support Services.</p>
    </article>
    <article class="finding tinted">
      <span class="num">02</span>
      <h3>INNOVATIVE APPROACHES TO TEMPORARY HOUSING</h3>
      <p>Innovative approaches to effective temporary housing practices are based upon the concept of resilient housing recovery, which has at least five dimensions: Wellbeing, Liveability, Sustainability, Community Connection, and Viability. This change of focus has two major implications:</p>
      <ul>
        <li>The planning of post-disaster housing and infrastructure programs needs to be become one of the priority strategies in pre-disaster preparation; and</li>
        <li>Strategies are needed to establish Temporary Housing as the first step in the design and construction of on-site Stable Housing to minimise the social.</li>
      </ul>
    </article>
    <article class="finding">
      <span class="num">03</span>
      <h3>A DECISION-MAKING FRAMEWORK FOR RESILIENT HOUSING RECOVERY</h3>
      <p>The Framework seeks to integrate the steps in project management and to use the housing process as a lever for overall recovery. This involves aligning decisions at strategic and operational levels and managing the trade-offs between issues of location, tenure, housing types and procurement. There are nine such decision categories in the Framework: Consultation, Pre-Disaster Planning for Housing Recovery, Situation Analysis after a Disaster Event, Recognising Cohorts of Displaced People with Different Needs and Assets, Identifying and Selecting Housing Model Options; Providing Agency Wrap-Around Support Services; Using Housing Decisions to Promote Local Economic and Social Recovery, Program Design and Delivery, and Monitoring and Evaluation.</p>
    </article>
  </section>

  <h2 class="recs-title">RECOMMENDATIONS</h2>

  <section class="recs-left">
    <div class="rec"><h4><svg class="hex" viewBox="0 0 14 14"><path d="M7 0l6 3.5v7L7 14 1 10.5v-7z" fill="#f5c536"/></svg>TERMINOLOGY</h4>
      <p>Develop a standard set of terminology to describe the phases and types of accommodation displaced people may access on the path to stable housing and to be adopted by State and Territory recovery agencies. The terms recommended for consideration are: Emergency and Short-Term Accommodation, Temporary Housing and Stable Housing.</p></div>
    <div class="rec"><h4><svg class="hex" viewBox="0 0 14 14"><path d="M7 0l6 3.5v7L7 14 1 10.5v-7z" fill="#f5c536"/></svg>PRINCIPLES</h4>
      <p>Develop a standard set of terminology to describe the phases and types of accommodation displaced people may access on the path to stable housing and to be adopted by State and Territory recovery agencies. The terms recommended for consideration are: Emergency and Short-Term Accommodation, Temporary Housing and Stable Housing.</p></div>
    <div class="rec"><h4><svg class="hex" viewBox="0 0 14 14"><path d="M7 0l6 3.5v7L7 14 1 10.5v-7z" fill="#f5c536"/></svg>NATIONAL PRINCIPLES</h4>
      <p>The Commonwealth and State/Territory governments should extend the agreed principles of disaster recovery to include principles of resilient recovery.</p></div>
    <div class="rec"><h4><svg class="hex" viewBox="0 0 14 14"><path d="M7 0l6 3.5v7L7 14 1 10.5v-7z" fill="#f5c536"/></svg>GUIDELINES</h4>
      <p>Develop resources and guidelines to support planning and operational response for post disaster temporary housing.</p></div>
    <div class="rec"><h4><svg class="hex" viewBox="0 0 14 14"><path d="M7 0l6 3.5v7L7 14 1 10.5v-7z" fill="#f5c536"/></svg>CAPACITY BUILDING</h4>
      <p>Develop capacity building resources and programs for State/Territory agencies and local governments to support pre planning for disaster temporary housing.</p></div>
    <div class="rec"><h4><svg class="hex" viewBox="0 0 14 14"><path d="M7 0l6 3.5v7L7 14 1 10.5v-7z" fill="#f5c536"/></svg>FUNDING</h4>
      <p>Recognise different cost implications of temporary housing programs including indirect costs. Develop funding streams to address the priority needs.</p></div>
  </section>

  <aside class="research">
    <h4><svg width="16" height="16" viewBox="0 0 14 14"><path d="M7 0l6 3.5v7L7 14 1 10.5v-7z" fill="#f5c536"/></svg>FURTHER RESEARCH</h4>
    <p class="intro">Undertake research into post disaster temporary housing topics such as:</p>
    <ul>
      <li>Improving housing resilience through land-use planning and building codes.</li>
      <li>Learnings from previous disasters on suitable approaches for different communities and contexts.</li>
      <li>Utilisation of innovative construction technologies, materials and methods.</li>
      <li>Utilising permanent prefabricated housing modules that transition from temporary to permanent.</li>
    </ul>
  </aside>

  <section class="recs-right">
    <div class="rec"><h4><svg class="hex" viewBox="0 0 14 14"><path d="M7 0l6 3.5v7L7 14 1 10.5v-7z" fill="#f5c536"/></svg>PILOT PROJECT</h4>
      <p>Resource, trial and evaluate a pilot program to identify ways of achieving a two-phase approach to assisting home-owners and renter households into stable housing.</p></div>
    <div class="rec"><h4><svg class="hex" viewBox="0 0 14 14"><path d="M7 0l6 3.5v7L7 14 1 10.5v-7z" fill="#f5c536"/></svg>DECISION MAKING FRAMEWORK</h4>
      <p>Adopt the outline of a Decision-Making Framework for Disaster Housing Recovery provided in this report to provide a basis for the development of tools that can be used by multiple stakeholders in housing recovery programs and projects across different parts of Australia.</p></div>
    <div class="rec"><h4><svg class="hex" viewBox="0 0 14 14"><path d="M7 0l6 3.5v7L7 14 1 10.5v-7z" fill="#f5c536"/></svg>CAPTURING LEARNINGS</h4>
      <p>Establish a national repository of evaluation reports and support processes for regular cross-case analysis.</p></div>
  </section>

  <section class="next">
    <div class="next-tab">NEXT STEPS</div>
    <p>The Community Recovery Advisory Group is partnering with Hazards Research Network to analyse previous post-disaster temporary housing assistance and support mechanisms used in Australia. The project aims to provide national guidance on the design and implementation of temporary housing from the research and resources developed.</p>
  </section>

  <footer class="contact">
    <h2>FOR FURTHER INFORMATION CONTACT:</h2>
    <div class="org">
      <span class="dot"></span>
      <span class="name">Community Recovery<br>Advisory Group<br>Australia</span>
    </div>
    <div class="person">
      <p class="who">HELEN MARSH</p>
      <p class="role">National Consultant Disaster Recovery<br>Community Recovery Advisory Group</p>
      <p class="mail"><svg width="10" height="8" viewBox="0 0 10 8"><rect width="10" height="8" rx="1" fill="#3aa0d6"/><path d="M0.5 1l4.5 3.5L9.5 1" stroke="#fff" fill="none" stroke-width="1"/></svg>helen.marsh@recoveryagency.gov.example</p>
    </div>
  </footer>

</main>
</body>
</html>
```